New letter head for Air Conditioning business

We need a new professional letter head design to suit our new re-branded air conditioning business. Our new logo is attached

```html
<!DOCTYPE html>
<html lang="en">
<head>
<meta charset="utf-8">
<title>Norvane Letterhead</title>
<link href="https://fonts.googleapis.com/css2?family=Open+Sans:wght@400;600;700&family=Mr+Dafoe&display=swap" rel="stylesheet">
<style>
  :root {
    --backdrop: #e8e8e8;
    --paper: #ffffff;
    --ink: #3b3e42;
    --ink-soft: #5a5d61;
    --coral: #ee6a5f;
    --charcoal: #2f3133;
    --mint: #4bb27a;
  }
  html, body {
    margin: 0;
    width: 1200px;
    height: 794px;
    overflow: hidden;
    background: var(--backdrop);
    font-family: "Open Sans", Arial, sans-serif;
    color: var(--ink);
  }
  .letterhead {
    position: absolute;
    left: 335px;
    top: 20px;
    width: 530px;
    height: 754px;
    background: var(--paper);
    box-shadow: 0 2px 10px rgba(0,0,0,.12);
  }
  .brand {
    position: absolute;
    left: 48px;
    top: 46px;
    display: flex;
    align-items: center;
    gap: 10px;
  }
  .brand-dot {
    width: 26px;
    height: 26px;
    border-radius: 50%;
    background: var(--coral);
  }
  .brand-name {
    font-size: 22px;
    font-weight: 600;
    letter-spacing: 3px;
    color: var(--ink);
    line-height: 1;
  }
  .brand-tagline {
    font-size: 6.5px;
    letter-spacing: 1px;
    color: var(--ink);
    margin-top: 3px;
    text-transform: uppercase;
  }
  .letter {
    position: absolute;
    left: 48px;
    top: 150px;
    width: 434px;
    font-size: 8.6px;
    line-height: 1.5;
    color: var(--ink-soft);
  }
  .letter-date, .recipient { color: var(--ink); font-size: 9.5px; }
  .recipient { margin: 12px 0 14px; line-height: 1.35; }
  .salutation { font-weight: 700; font-size: 10px; color: var(--ink); margin-bottom: 14px; }
  .letter p { margin: 0 0 14px; }
  .sign-off {
    position: absolute;
    right: 48px;
    top: 495px;
    text-align: right;
    font-size: 9px;
    color: var(--ink);
    line-height: 1.35;
  }
  .signature {
    font-family: "Mr Dafoe", cursive;
    font-size: 26px;
    line-height: 1;
    margin: 4px 0 4px;
  }
  .contact-line {
    position: absolute;
    left: 48px;
    right: 30px;
    bottom: 58px;
    display: flex;
    gap: 10px;
    font-size: 8.3px;
    color: var(--ink);
    align-items: center;
  }
  .contact-item { display: flex; align-items: center; gap: 3px; white-space: nowrap; }
  .contact-icon { width: 9px; height: 9px; }
  .footer-band {
    position: absolute;
    left: 0; right: 0; bottom: 0;
    height: 50px;
    background: var(--coral);
  }
  .address-tab {
    position: absolute;
    right: 52px;
    bottom: 30px;
    height: 18px;
    padding: 0 18px 0 16px;
    background: var(--charcoal);
    color: #fff;
    font-size: 8.3px;
    display: flex;
    align-items: center;
    gap: 5px;
    clip-path: polygon(0 0, 100% 0, calc(100% - 8px) 100%, 8px 100%);
  }
</style>
</head>
<body>
  <main class="letterhead">
    <header class="brand">
      <span class="brand-dot"></span>
      <div>
        <div class="brand-name">NORVANE</div>
        <div class="brand-tagline">Cooling &amp; Refrigeration</div>
      </div>
    </header>

    <section class="letter">
      <div class="letter-date">January 03, 2017</div>
      <div class="recipient">
        Mr. Alan Pryce<br>President<br>Pryce Holdings<br>48 Mill Lane, Suite 5<br>Lenfield, WA, 60412
      </div>
      <div class="salutation">Dear Mr. Alan,</div>
      <p>Lorem Ipsum is simply dummy text of the printing and typesetting industry. Lorem Ipsum has been the industry's standard dummy text ever since the 1500s, when an unknown printer took a galley of type and scrambled it to make a type specimen book. It has survived not only five centuries, but also the leap into electronic typesetting, remaining essentially unchanged.</p>
      <p>The standard chunk of Lorem Ipsum used since the 1500s is reproduced below for those interested. Sections 1.10.32 and 1.10.33 from "Notes on Quiet Engines" by Orin Valdess are also reproduced in their exact original form, accompanied by English versions from the 1914 translation by T. Halvey.</p>
      <p>Lorem Ipsum is simply dummy text of the printing and typesetting industry. Lorem Ipsum has been the industry's standard dummy text ever since the 1500s, when an unknown printer took a galley of type and scrambled it to make a type specimen book. It has survived not only five centuries, but also the leap into electronic typesetting, remaining essentially unchanged. It was popularised in the</p>
    </section>

    <div class="sign-off">
      Sincerely Yours,
      <div class="signature">your name</div>
      Name Last Name<br>Company Name
    </div>

    <div class="contact-line">
      <span class="contact-item"><svg class="contact-icon" viewBox="0 0 10 10"><circle cx="5" cy="5" r="5" fill="var(--mint)"/><path d="M3.3 2.6l1 1-.5.7a3.5 3.5 0 0 0 1.9 1.9l.7-.5 1 1-.6.8C4.9 7.3 2.7 5.1 2.5 3.2z" fill="#fff"/></svg>(00) 05521 384 907</span>
      <span class="contact-item"><svg class="contact-icon" viewBox="0 0 10 10"><circle cx="5" cy="5" r="5" fill="var(--mint)"/><path d="M3.3 2.6l1 1-.5.7a3.5 3.5 0 0 0 1.9 1.9l.7-.5 1 1-.6.8C4.9 7.3 2.7 5.1 2.5 3.2z" fill="#fff"/></svg>(00) 05521 384 908</span>
      <span class="contact-item"><svg class="contact-icon" viewBox="0 0 10 10"><circle cx="5" cy="5" r="5" fill="var(--mint)"/><rect x="2.5" y="3.2" width="5" height="3.6" fill="#fff"/><path d="M2.5 3.2L5 5.2 7.5 3.2" stroke="var(--mint)" stroke-width=".6" fill="none"/></svg>hello@norvaneair.com</span>
      <span class="contact-item"><svg class="contact-icon" viewBox="0 0 10 10"><circle cx="5" cy="5" r="5" fill="var(--mint)"/><rect x="2.5" y="3.2" width="5" height="3.6" fill="#fff"/><path d="M2.5 3.2L5 5.2 7.5 3.2" stroke="var(--mint)" stroke-width=".6" fill="none"/></svg>hello@norvaneair.com</span>
    </div>

    <div class="footer-band"></div>
    <div class="address-tab">
      <svg class="contact-icon" viewBox="0 0 10 10"><circle cx="5" cy="5" r="5" fill="var(--coral)"/><path d="M5 2a2 2 0 0 0-2 2c0 1.5 2 3.8 2 3.8S7 5.5 7 4a2 2 0 0 0-2-2z" fill="#fff"/><circle cx="5" cy="4" r=".7" fill="var(--coral)"/></svg>
      Unit 14 Harbour Road, Lenfield, Zip 6041, Country
    </div>
  </main>
</body>
</html>
```